Coral Bay Pools New website

I currently operate a swimming pool service and repair business and looking for a re design for my website as it has been over 5 years since it was designed. current site is coralbaypoolslv.com

```html
<!DOCTYPE html>
<html lang="en">
<head>
<meta charset="utf-8">
<title>Coral Bay Pools</title>
<link href="https://fonts.googleapis.com/css2?family=Poppins:ital,wght@0,400;0,500;0,600;0,700;0,800;1,700&family=Allura&display=swap" rel="stylesheet">
<style>
:root{
  --navy:#0b5ea6;
  --deep:#084780;
  --ink:#0a3f73;
  --sky:#2aa8e2;
  --orange:#f8a928;
  --white:#ffffff;
  --text:#1f2d3d;
  --copy-bar:#1b7cc5;
}
*{box-sizing:border-box;margin:0;padding:0}
html,body{width:1200px;height:5286px;overflow:hidden}
body{font-family:'Poppins',sans-serif;color:var(--text);background:var(--white);position:relative}
.abs,.photo{position:absolute}

/* header */
.site-header{position:absolute;top:0;left:0;width:1200px;height:140px;z-index:5}
.brand{position:absolute;left:78px;top:52px;display:flex;align-items:center;gap:12px;font-weight:700;font-size:30px;color:var(--navy)}
.brand-dot{width:34px;height:34px;border-radius:50%;background:var(--orange);flex:none}
.nav{position:absolute;right:94px;top:56px;display:flex;align-items:center;gap:44px;font-size:13px;font-weight:500;color:#1d2b3a}
.nav .cta{background:var(--orange);color:var(--white);padding:10px 18px;border-radius:22px}

/* hero */
.hero{position:absolute;top:0;left:0;width:1200px;height:990px}
.hero-ring{position:absolute;left:338px;top:216px;width:524px;height:524px;border:3px solid var(--navy);border-radius:50%}
.hero-badge{position:absolute;left:354px;top:232px;width:492px;height:492px;border-radius:50%;background:var(--navy);text-align:center;color:var(--white)}
.hero-welcome{font-family:'Allura',cursive;font-size:66px;margin-top:86px;line-height:1}
.hero-title{font-size:42px;font-weight:500;margin-top:14px;letter-spacing:.5px}
.hero-sub{font-size:21px;font-weight:600;margin-top:24px;line-height:1.35}
.btn-sky{display:inline-block;margin-top:40px;background:var(--sky);color:var(--white);font-weight:600;font-size:21px;padding:14px 30px;border-radius:4px 28px 4px 28px}

/* feature band */
.features{position:absolute;top:965px;left:0;width:1200px;height:235px;background:linear-gradient(180deg,#2b9fd8,#1b83c6)}
.feature-list{position:absolute;top:1033px;left:0;width:1200px;display:flex;justify-content:center;gap:22px}
.feature{width:170px;text-align:center;color:var(--white);font-size:15px;line-height:1.25}
.feature-icon{width:96px;height:96px;border-radius:50%;background:var(--white);border:4px solid #9fdcf7;margin:0 auto 12px;display:flex;align-items:center;justify-content:center}
.feature-icon span{width:48px;height:48px;border-radius:10px;background:#cbe9f8}

/* about */
.about{position:absolute;top:1200px;left:0;width:1200px;height:645px;background:linear-gradient(180deg,#2aa9e3 0%,#1a7fc4 60%,#0f63aa 100%)}
.about-title{position:absolute;left:667px;top:1322px;font-size:46px;font-weight:700;color:var(--white);line-height:1}
.kicker{position:absolute;font-size:19px;color:var(--orange);font-weight:500;display:flex;align-items:center;gap:10px}
.kicker::after{content:"";width:42px;height:2px;background:var(--orange)}
.about-lead{position:absolute;left:667px;top:1423px;width:495px;font-size:26px;color:var(--white);line-height:1.3;letter-spacing:.3px}
.about-body{position:absolute;left:667px;top:1508px;width:480px;font-size:12.5px;color:var(--white);line-height:1.95}
.btn-orange{position:absolute;background:var(--orange);color:var(--white);font-size:18px;font-weight:500;padding:16px 36px;border-radius:26px 4px 26px 4px}

/* services */
.services{position:absolute;top:1845px;left:0;width:1200px;height:1950px;background:linear-gradient(180deg,#ffffff 0%,#e6f6fd 18%,#a4e1f9 45%,#6bd0f7 75%,#4fc4f4 100%)}
.section-title{position:absolute;left:0;width:1200px;text-align:center;font-size:48px;font-weight:700;color:var(--ink);top:1975px}
.section-kicker{position:absolute;left:0;width:1200px;top:2038px;display:flex;justify-content:center;align-items:center;gap:10px;color:var(--orange);font-size:21px}
.section-kicker i{display:block;width:78px;height:2px;background:var(--orange)}
.pill-heading{position:absolute;background:var(--navy);color:var(--white);font-weight:700;font-size:30px;padding:12px 30px 12px 60px;border-radius:30px 10px 30px 10px;white-space:nowrap}
.svc-body{position:absolute;font-size:12.5px;line-height:1.8;color:#1d2b3a}
.svc-body p+p{margin-top:22px}
.ticks{list-style:none;margin-top:10px}
.ticks li{display:flex;align-items:center;gap:10px;font-weight:600;font-size:12.5px;margin-bottom:6px}
.btn-navy{position:absolute;background:var(--navy);color:var(--white);font-weight:600;font-size:18px;padding:16px 34px;border-radius:26px 4px 26px 4px}

/* why */
.why{position:absolute;top:3795px;left:0;width:1200px;height:552px;background:var(--navy)}
.why-title{position:absolute;left:66px;top:3905px;font-size:45px;font-weight:700;color:var(--white)}
.why-rule{position:absolute;left:66px;top:3982px;width:110px;height:3px;background:var(--white)}
.why-strong{position:absolute;left:66px;top:4010px;width:470px;font-size:18px;font-weight:600;color:var(--white);line-height:1.65}
.why-light{position:absolute;left:66px;top:4152px;width:430px;font-size:24px;color:var(--white);line-height:1.3}
.why-cta{position:absolute;left:66px;top:4282px;font-size:19px;font-weight:700;font-style:italic;color:var(--orange)}

/* contact */
.contact{position:absolute;top:4347px;left:0;width:1200px;height:553px}
.contact-title{position:absolute;left:628px;top:4465px;font-size:46px;font-weight:700;color:var(--ink)}
.contact-kicker{color:var(--navy)}
.contact-kicker::after{width:90px}
.field{position:absolute;background:var(--white);border:1px solid #dfe3e8;font-size:12px;color:#333;padding:12px 18px}
.btn-submit{position:absolute;left:640px;top:4778px;width:156px;height:52px;background:var(--orange);color:var(--white);font-size:17px;font-weight:500;display:flex;align-items:center;justify-content:center;border-radius:26px 4px 26px 4px}

/* footer */
.footer{position:absolute;top:4900px;left:0;width:1200px;height:386px;background:var(--deep)}
.footer-brand{position:absolute;left:66px;top:5085px;font-size:27px;font-weight:700;color:var(--white);display:flex;align-items:center;gap:12px}
.vrule{position:absolute;top:5020px;width:2px;height:190px;background:rgba(255,255,255,.6)}
.vrule::before{content:"";position:absolute;left:-3px;top:-6px;width:8px;height:8px;border-radius:50%;background:var(--white)}
.f-head{position:absolute;top:5025px;font-size:16px;font-weight:500;color:var(--white)}
.f-links{position:absolute;left:382px;top:5080px;list-style:none;font-size:13px;line-height:2.05;color:var(--white)}
.f-contact{position:absolute;left:592px;display:flex;gap:16px;font-size:12.5px;line-height:1.3;color:var(--white)}
.f-icon{width:26px;height:26px;border:1.5px solid var(--white);border-radius:3px;display:flex;align-items:center;justify-content:center;flex:none}
.f-news{position:absolute;left:886px;top:5088px;width:230px;font-size:13px;line-height:1.4;color:var(--white)}
.f-input{position:absolute;left:884px;top:5147px;width:204px;height:36px;border:1.5px solid var(--white);border-radius:18px;font-size:11px;padding:10px 18px;color:var(--white)}
.f-go{position:absolute;right:6px;top:4px;width:24px;height:24px;border:1.5px solid var(--white);border-radius:50%;display:flex;align-items:center;justify-content:center}
.copyright{position:absolute;top:5236px;left:0;width:1200px;height:50px;background:var(--copy-bar);text-align:center;font-size:14px;line-height:50px;color:var(--white)}
</style>
</head>
<body>

<section class="hero">
  <div class="photo" style="inset:0;background:linear-gradient(160deg,#f2f4f6 0%,#d9e5ec 30%,#6fc7df 55%,#1e97c6 80%,#0f77aa 100%)" role="img" aria-label="Resort pool with loungers, umbrellas and a water fountain"></div>
  <div class="hero-ring"></div>
  <div class="hero-badge">
    <div class="hero-welcome">Welcome To</div>
    <div class="hero-title">CORAL BAY POOLS</div>
    <div class="hero-sub">NEVADA'S TRUSTED<br>LOCAL POOL CLEANING</div>
    <div class="btn-sky">FREE ESTIMATE</div>
  </div>
</section>

<header class="site-header">
  <div class="brand"><span class="brand-dot"></span>Coral Bay Pools</div>
  <nav class="nav">
    <span>HOME</span><span>ABOUT US</span><span>OUR SERVICES</span><span>BLOG</span><span>FREE ESTIMATE</span><span class="cta">CONTACT US</span>
  </nav>
</header>

<section class="features">
  <svg class="abs" style="top:-30px;left:0" width="1200" height="40" viewBox="0 0 1200 40" preserveAspectRatio="none"><path d="M0 30 Q150 10 300 28 T600 26 T900 30 T1200 24 V40 H0Z" fill="#2b9fd8"/><path d="M0 30 Q150 10 300 28 T600 26 T900 30 T1200 24" fill="none" stroke="#ffffff" stroke-width="6"/></svg>
</section>
<div class="feature-list">
  <div class="feature"><div class="feature-icon" role="img" aria-label="Pool vacuum icon"><span></span></div>Vacuum and<br>brush your pool</div>
  <div class="feature"><div class="feature-icon" role="img" aria-label="Tile cleaning icon"><span></span></div>Thoroughly<br>clean the tiles</div>
  <div class="feature"><div class="feature-icon" role="img" aria-label="Chemicals icon"><span></span></div>Balance the<br>chemicals</div>
  <div class="feature"><div class="feature-icon" role="img" aria-label="Skimmer basket icon"><span></span></div>Remove and clean<br>all the baskets</div>
  <div class="feature"><div class="feature-icon" role="img" aria-label="Pool filter icon"><span></span></div>Clean the filter<br>when necessary</div>
</div>

<section class="about">
  <div class="photo" style="left:0;top:62px;width:605px;height:526px;background:linear-gradient(180deg,#e9d9b8 0%,#9cc38a 25%,#4ab9e0 50%,#1a8ad0 100%)" role="img" aria-label="Hotel pool with sun loungers and palm trees"></div>
</section>
<h2 class="about-title">ABOUT US</h2>
<div class="kicker" style="left:667px;top:1374px">CORAL BAY POOLS</div>
<p class="about-lead">We are a full service pool company servicing the Las Vegas Valley</p>
<p class="about-body">When you need professional pool cleaning services in Nevada, you can count on the professionals at Coral Bay Pools to provide you with superior and prompt solutions. Whether you need assistance with a residential or commercial pool, we'll vacuum, brush, and thoroughly clean your pool so it's swim-ready. We'll also clean your pool filters and inform you of any issues that arise.</p>
<div class="btn-orange" style="left:664px;top:1690px">LEARN MORE</div>
<svg class="abs" style="top:1836px;left:0" width="1200" height="20" viewBox="0 0 1200 20" preserveAspectRatio="none"><path d="M0 8 Q100 2 200 9 T400 7 T600 10 T800 6 T1000 9 T1200 7 V20 H0Z" fill="#ffffff"/></svg>

<section class="services"></section>
<h2 class="section-title">OUR SERVICES</h2>
<div class="section-kicker"><i></i>WHAT WE DO<i></i></div>

<div class="pill-heading" style="left:28px;top:2135px">POOL SERVICES</div>
<div class="svc-body" style="left:66px;top:2218px;width:480px">
  <p>When you invested in your pool, you knew it was a long-term investment in both money and time. At home, it's an oasis, a place to beat the heat and relax. At your business, it's both an accessory for the enjoyment of your clients as well as an important design element.</p>
  <p>To have your pool cleaned just right, contact the professionals at Coral Bay Pools. With more than ten years of industry experience, our team of certified pool operators will:</p>
  <ul class="ticks">
    <li><svg width="18" height="18" viewBox="0 0 18 18"><circle cx="9" cy="9" r="7.5" fill="none" stroke="#1d2b3a" stroke-width="1.6"/><path d="M5.5 9.2l2.4 2.4 4.6-4.8" fill="none" stroke="#1d2b3a" stroke-width="1.8"/></svg>Vacuum and brush your pool</li>
    <li><svg width="18" height="18" viewBox="0 0 18 18"><circle cx="9" cy="9" r="7.5" fill="none" stroke="#1d2b3a" stroke-width="1.6"/><path d="M5.5 9.2l2.4 2.4 4.6-4.8" fill="none" stroke="#1d2b3a" stroke-width="1.8"/></svg>Thoroughly clean the tiles</li>
    <li><svg width="18" height="18" viewBox="0 0 18 18"><circle cx="9" cy="9" r="7.5" fill="none" stroke="#1d2b3a" stroke-width="1.6"/><path d="M5.5 9.2l2.4 2.4 4.6-4.8" fill="none" stroke="#1d2b3a" stroke-width="1.8"/></svg>Balance the chemicals</li>
  </ul>
</div>
<div class="btn-navy" style="left:68px;top:2508px">KNOW MORE</div>
<div class="photo" style="left:619px;top:2124px;width:516px;height:425px;background:linear-gradient(135deg,#5fd0f5,#1a9de0 60%,#0d7fc8)" role="img" aria-label="Pool skimmer net over clear blue water"></div>

<div class="photo" style="left:68px;top:2635px;width:541px;height:425px;background:linear-gradient(160deg,#8fa9b8,#4f7e97 50%,#2f607b)" role="img" aria-label="Robotic cleaner on pool steps underwater"></div>
<div class="pill-heading" style="left:640px;top:2650px;padding-left:18px;padding-right:24px">COMMERCIAL POOL SERVICES</div>
<div class="svc-body" style="left:664px;top:2730px;width:470px">
  <p>As a commercial property owner or manager, doing your job well requires you to be mindful of all the details. Every day is filled with a thousand different decisions, and when you need support for your facility,</p>
  <p>it's critical that the company you rely upon be prompt and responsive. In fact, one of the main reasons businesses end up switching pool cleaning companies is "my pool guy never picks up the phone."</p>
</div>
<div class="btn-navy" style="left:664px;top:2950px">KNOW MORE</div>

<div class="pill-heading" style="left:28px;top:3195px;padding-left:34px">RESIDENTIAL POOL SERVICES</div>
<div class="svc-body" style="left:66px;top:3276px;width:480px">
  <p>Here in Southern Nevada, you know it can get really, really hot. That's why you invested in your pool at home; so that you would always have a place to cool off and relax with family and friends. You want your pool to look its best and function well, but to make that happen, you need to have it cleaned and serviced regularly.</p>
  <p>The trick is working with a company that can keep your pool looking good and that has the technical knowledge to handle the problems that</p>
</div>
<div class="btn-navy" style="left:68px;top:3502px">KNOW MORE</div>
<div class="photo" style="left:619px;top:3183px;width:516px;height:424px;background:linear-gradient(180deg,#3e8fd6 0%,#8fc3e6 45%,#c9b28e 70%,#39b8e4 100%)" role="img" aria-label="Children jumping into a backyard pool"></div>

<section class="why">
  <div class="photo" style="left:600px;top:0;width:600px;height:552px;background:linear-gradient(180deg,#d8e4dc 0%,#9fc6c6 35%,#3f8fbf 70%,#1e6aa6 100%)" role="img" aria-label="Steel pool ladder into blue water"></div>
</section>
<h2 class="why-title">WHY CHOOSE US?</h2>
<div class="why-rule"></div>
<p class="why-strong">Our full-service pool company proudly serves the entire Las Vegas valley, and we're certified by the Desert Valley Health Board to maintain the highest level of pool safety</p>
<p class="why-light">If you need repairs, maintenance, scheduled cleanings, or any other pool services,</p>
<p class="why-cta">CONTACT US ONLINE OR BY PHONE TODAY.</p>

<section class="contact">
  <div class="photo" style="inset:0;background:linear-gradient(180deg,#fdf4f6 0%,#f3d6e2 45%,#c4a0c2 65%,#6aaed0 85%,#3b8fc0 100%)" role="img" aria-label="Resort pool with steel handrails at sunset"></div>
</section>
<h2 class="contact-title">CONTACT US</h2>
<div class="kicker contact-kicker" style="left:630px;top:4526px">CORAL BAY POOLS</div>
<div class="field" style="left:632px;top:4570px;width:236px;height:40px">Your Name</div>
<div class="field" style="left:878px;top:4570px;width:236px;height:40px">Phone Number</div>
<div class="field" style="left:632px;top:4622px;width:482px;height:42px">Email Address</div>
<div class="field" style="left:632px;top:4677px;width:482px;height:80px">Message</div>
<div class="btn-submit">SUBMIT</div>

<footer class="footer"></footer>
<div class="footer-brand"><span class="brand-dot"></span>Coral Bay Pools</div>
<div class="vrule" style="left:338px"></div>
<div class="vrule" style="left:548px"></div>
<div class="vrule" style="left:850px"></div>
<div class="f-head" style="left:380px">QUICK LINKS</div>
<ul class="f-links"><li>» About Us</li><li>» Services</li><li>» Testimonials</li><li>» Blog</li><li>» Contact Us</li></ul>
<div class="f-head" style="left:592px">CONTACT US</div>
<div class="f-contact" style="top:5075px"><span class="f-icon"><svg width="14" height="14" viewBox="0 0 24 24"><path d="M6 3l4 4-2 3a12 12 0 006 6l3-2 4 4-3 3C10 21 3 14 3 6z" fill="#fff"/></svg></span><span>CALL US<br>555 014 2290</span></div>
<div class="f-contact" style="top:5133px"><span class="f-icon"><svg width="14" height="14" viewBox="0 0 24 24"><rect x="3" y="6" width="18" height="12" fill="#fff"/><path d="M3 6l9 7 9-7" fill="none" stroke="#084780" stroke-width="2"/></svg></span><span>EMAIL US<br>info@coralbaypoolslv.com</span></div>
<div class="f-contact" style="top:5188px"><span class="f-icon"><svg width="14" height="14" viewBox="0 0 24 24"><path d="M12 2a7 7 0 00-7 7c0 5 7 13 7 13s7-8 7-13a7 7 0 00-7-7z" fill="#fff"/><circle cx="12" cy="9" r="2.5" fill="#084780"/></svg></span><span>Address line Dummy Here<br>Address line Here</span></div>
<div class="f-head" style="left:882px">NEWSLETTER SIGN UP</div>
<p class="f-news">Subscribe our newsletter to get the latest news.</p>
<div class="f-input">Enter Email Address<span class="f-go"><svg width="12" height="12" viewBox="0 0 12 12"><path d="M1 6h9M7 3l3 3-3 3" fill="none" stroke="#fff" stroke-width="1.5"/></svg></span></div>
<div class="copyright">Copyright © 2026 All Rights Reserved By Coral Bay Pools</div>

</body>
</html>
```